RESIDENTIAL CONSTRUCTION

We are a company that specializes in building custom residential homes, the design should also emphasize that quality and service is our priority.

Industry/Entity Type

Construction Company

Contact Information for Business Card

Contact Person: Marcus Lindqvist
Company Address: 273 West Alder Ave San Jose , Ca 95380
Phone Number : 408-731-2946
Email Address: Stoneridgehomes517@mailvista.net

Font styles to use
Sans Serif

Colors
ec1f27

Requirements
Must have
• CSLB # 7362015
Nice to have
• needs to have same color as logo i uploaded, we will be printing these on a clear plastic card.

```html
<!DOCTYPE html>
<html lang="en">
<head>
<meta charset="utf-8">
<title>Stoneridge Homes – Business Card</title>
<link rel="stylesheet" href="https://fonts.googleapis.com/css2?family=Oswald:wght@500;600&family=Arimo:wght@400;700&display=swap">
<style>
  :root {
    --brand-red: #ec1f27;
    --deep-red: #b8121a;
    --ink: #1b1b1b;
    --card-base: #f2f2f2;
    --card-shade: #e2e3e5;
    --page-bg: #d9d6d1;
  }
  * { margin: 0; padding: 0; box-sizing: border-box; }
  html, body {
    width: 1200px; height: 970px; overflow: hidden;
    background: var(--page-bg);
  }
  .business-card {
    position: absolute; left: 80px; top: 190px;
    width: 1040px; height: 590px;
    border-radius: 30px; overflow: hidden;
    background: linear-gradient(160deg, var(--card-base) 0%, #fafafa 45%, var(--card-shade) 100%);
    box-shadow: 0 10px 30px rgba(0,0,0,0.18);
  }
  .card-swoosh { position: absolute; left: 0; top: 0; width: 1040px; height: 590px; }
  .name-block {
    position: absolute; right: 46px; top: 56px;
    text-align: right;
  }
  .contact-name {
    font-family: "Oswald", sans-serif; font-weight: 600;
    font-size: 42px; line-height: 52px; letter-spacing: -0.5px; color: var(--ink);
    text-transform: uppercase; transform: scaleX(0.86); transform-origin: right center;
  }
  .license {
    margin-top: 4px;
    font-family: "Arimo", Arial, sans-serif; font-weight: 700;
    font-size: 20px; line-height: 26px; letter-spacing: 0.5px; color: var(--ink);
  }
  .brand {
    position: absolute; left: 52px; top: 250px;
    display: flex; align-items: center; gap: 18px;
  }
  .brand-mark { width: 64px; height: 64px; background: var(--brand-red); flex: none; }
  .brand-name {
    font-family: "Oswald", sans-serif; font-weight: 600;
    font-size: 64px; line-height: 1; color: var(--brand-red);
    text-transform: uppercase; white-space: nowrap;
  }
  .divider {
    position: absolute; left: 52px; top: 439px;
    width: 920px; height: 2px; background: var(--brand-red);
  }
  .contact-list, .address {
    position: absolute; top: 472px;
    font-family: "Arimo", Arial, sans-serif; font-size: 27px;
    line-height: 38px; color: var(--ink); list-style: none;
  }
  .contact-list { left: 52px; }
  .contact-list li { display: flex; align-items: center; gap: 12px; white-space: nowrap; }
  .contact-list svg { width: 22px; height: 22px; flex: none; }
  .address { left: 722px; font-style: normal; white-space: nowrap; }
</style>
</head>
<body>
  <article class="business-card">
    <svg class="card-swoosh" viewBox="0 0 1040 590" aria-hidden="true">
      <defs>
        <linearGradient id="redBand" x1="0" y1="0" x2="1" y2="0.4">
          <stop offset="0" stop-color="#ec1f27"/>
          <stop offset="0.5" stop-color="#b8121a"/>
          <stop offset="1" stop-color="#e31b23"/>
        </linearGradient>
      </defs>
      <path d="M0 0 H1040 V372 C930 230 700 80 30 72 L0 74 Z" fill="url(#redBand)"/>
      <path d="M25 86 C520 40 880 190 1040 440 L1040 412 C870 170 520 40 25 86 Z" fill="#161616"/>
    </svg>

    <div class="name-block">
      <h1 class="contact-name">Marcus Lindqvist</h1>
      <p class="license">CSLB # 7362015</p>
    </div>

    <div class="brand">
      <span class="brand-mark"></span>
      <span class="brand-name">Stoneridge Homes</span>
    </div>

    <div class="divider"></div>

    <ul class="contact-list">
      <li>
        <svg viewBox="0 0 24 24" aria-hidden="true"><path fill="#ec1f27" d="M6.6 10.8c1.4 2.8 3.8 5.1 6.6 6.6l2.2-2.2c.3-.3.7-.4 1-.2 1.1.4 2.3.6 3.6.6.6 0 1 .4 1 1V20c0 .6-.4 1-1 1C10.6 21 3 13.4 3 4c0-.6.4-1 1-1h3.5c.6 0 1 .4 1 1 0 1.3.2 2.5.6 3.6.1.3 0 .7-.2 1z"/></svg>
        <span>408-731-2946</span>
      </li>
      <li>
        <svg viewBox="0 0 24 24" aria-hidden="true"><rect x="2" y="5" width="20" height="14" fill="#ec1f27"/><path d="M2 5 L12 13 L22 5" fill="none" stroke="#f2f2f2" stroke-width="1.6"/></svg>
        <span>Stoneridgehomes517@mailvista.net</span>
      </li>
    </ul>

    <address class="address">
      273 West Alder Ave<br>
      San Jose, Ca 95380
    </address>
  </article>
</body>
</html>
```